Tech Savy small Business accountant business card design

We need a business card for a new company based in the cloud. We provide tax, business advisory, accounting, information technology solutions and back office functions to small businesses. We offer fixed fee packages with add on services as you need them. By harnessing technology we simplify small business operational processes providing valuable time and information for small business owners to grow their business. In the logo (bluvoria) we want to be able to see bluv and experts. The final design should communicate achieving growth dreams and balance (ie life and $).
Updates
This project has been temporarily placed on hold until I finalize "Tech Savy small Business accountant needs a logo". I invite all designers to submit on this logo project. Once my logo is finalized I will resume this business card contest. Thanks Added Wednesday, March 19, 2014
This project has been temporarily placed on hold until I finalize "Tech Savy small Business accountant logo". I invite all designers to submit on this logo project. Once my logo is finalized I will resume this business card contest. Thanks Added Thursday, March 20, 2014
Target Market(s)
Small Business (Revenue $500,000, more than 3 employees) owners.
Industry/Entity Type
Small Business
Contact Information for Business Card
Marcy Elwind (Principal)
Accountant, Tax Agent.
TEL | 0417 683 912
EMAIL | Marcy.Elwind@bluvoria.com.au
WEB | www.bluvoria.com.au
Look and feel

```html
<!DOCTYPE html>
<html lang="en">
<head>
<meta charset="utf-8">
<title>bluvoria business card</title>
<link rel="stylesheet" href="https://fonts.googleapis.com/css2?family=Questrial&display=swap">
<style>
  :root {
    --bg: #e9ebee;
    --paper: #f7f7f7;
    --blue: #1aa3d3;
    --blue-light: #20b8e3;
    --blue-deep: #1282b5;
    --grey: #8c8d90;
    --grey-dark: #7a7b7e;
    --white: #ffffff;
  }
  * { box-sizing: border-box; margin: 0; padding: 0; }
  html, body {
    width: 1200px; height: 780px; overflow: hidden;
    background: var(--bg);
    font-family: "Questrial", "Century Gothic", sans-serif;
  }
  .sheet {
    width: 1200px; height: 780px;
    display: flex; align-items: center; justify-content: center; gap: 40px;
  }
  .card {
    position: relative;
    width: 540px; height: 309px;
    overflow: hidden;
    box-shadow: 0 6px 18px rgba(0,0,0,0.18);
  }

  /* Front */
  .card-front { background: var(--paper); }
  .brand {
    position: absolute; left: 44px; top: 38px;
    display: flex; align-items: center; gap: 12px;
  }
  .brand-dot {
    width: 22px; height: 22px; border-radius: 50%;
    background: var(--blue);
  }
  .brand-name {
    font-size: 66px; line-height: 1; color: var(--grey);
    letter-spacing: -1px;
  }
  .tagline {
    position: absolute; left: 78px; top: 112px;
    font-size: 17px; color: var(--grey); letter-spacing: 0.5px;
  }
  .contact-band {
    position: absolute; left: 0; right: 0; top: 162px; height: 92px;
    background: linear-gradient(180deg, var(--blue-light), var(--blue));
    display: flex; align-items: center;
    color: var(--white);
  }
  .person { width: 232px; padding-left: 34px; }
  .person-name { font-size: 24px; line-height: 1.05; }
  .person-role { font-size: 12px; text-align: right; padding-right: 14px; line-height: 1.1; }
  .person-title { font-size: 14px; margin-top: 4px; }
  .band-divider { width: 2px; height: 58px; background: var(--white); margin-right: 14px; }
  .contact-list { list-style: none; font-size: 13.5px; line-height: 1.55; }
  .contact-list li { display: flex; align-items: center; gap: 7px; }
  .contact-icon { width: 13px; height: 13px; flex: none; }
  .address {
    position: absolute; left: 250px; top: 270px;
    font-size: 14px; color: var(--grey);
  }

  /* Back */
  .card-back {
    background: radial-gradient(ellipse at 55% 50%, var(--blue-light), var(--blue) 55%, var(--blue-deep));
  }
  .back-band {
    position: absolute; left: 0; right: 0; top: 82px; height: 145px;
    background: var(--paper);
    display: flex; flex-direction: column; align-items: center; justify-content: center;
  }
  .back-band .brand { position: static; }
  .back-band .tagline { position: static; margin-top: 8px; }
</style>
</head>
<body>
<main class="sheet">
  <section class="card card-front" aria-label="Card front">
    <div class="brand">
      <span class="brand-dot"></span>
      <span class="brand-name">bluvoria</span>
    </div>
    <p class="tagline">Your business and accounting partner</p>

    <div class="contact-band">
      <div class="person">
        <p class="person-name">Marcy Elwind</p>
        <p class="person-role">(Principal)</p>
        <p class="person-title">Accountant, Tax Agent</p>
      </div>
      <span class="band-divider"></span>
      <ul class="contact-list">
        <li>
          <svg class="contact-icon" viewBox="0 0 16 16" aria-hidden="true">
            <rect x="0.5" y="0.5" width="15" height="15" rx="2" fill="none" stroke="#fff"/>
            <path d="M5 3.5l2 2-1.2 1.2c.6 1.4 1.6 2.4 3 3L10 8.5l2 2-1.5 1.8C7 12 4 9 3.7 5.2z" fill="#fff"/>
          </svg>
          <span>0417 683 912</span>
        </li>
        <li>
          <svg class="contact-icon" viewBox="0 0 16 16" aria-hidden="true">
            <rect x="0.5" y="0.5" width="15" height="15" rx="2" fill="none" stroke="#fff"/>
            <rect x="3" y="4.5" width="10" height="7" fill="none" stroke="#fff"/>
            <path d="M3 4.5l5 4 5-4" fill="none" stroke="#fff"/>
          </svg>
          <span>Marcy.Elwind@bluvoria.com.au</span>
        </li>
        <li>
          <svg class="contact-icon" viewBox="0 0 16 16" aria-hidden="true">
            <rect x="0.5" y="0.5" width="15" height="15" rx="2" fill="none" stroke="#fff"/>
            <circle cx="8" cy="8" r="4.5" fill="none" stroke="#fff"/>
            <ellipse cx="8" cy="8" rx="2" ry="4.5" fill="none" stroke="#fff"/>
            <path d="M3.5 8h9" stroke="#fff"/>
          </svg>
          <span>www.bluvoria.com.au</span>
        </li>
      </ul>
    </div>

    <p class="address">Harbourview NSW Australia</p>
  </section>

  <section class="card card-back" aria-label="Card back">
    <div class="back-band">
      <div class="brand">
        <span class="brand-dot"></span>
        <span class="brand-name">bluvoria</span>
      </div>
      <p class="tagline">Your business and accounting partner</p>
    </div>
  </section>
</main>
</body>
</html>
```